Harbor Crest Holdings Corporate Showcase

Provide an attractive Corporate Website for a boutique Investment Company to showcase our activities and corporate interests.

Our Company works across a number of Sectors including

Real Estate
E-Commerce
Healthcare
Beauty & Personal Care
Technology
Resources

Lets keep the personality

Modern
Global
Sophisticated
Calm
Interesting

Lets keep the pages with MINIMAL Words
Lets use Photos/ Imagery to tell the story

We'll need a Banner Menu -
About Us
Expertise
Global Outlook
Sectors
Management
Media
Contact Us

Many thanks
Best wishes
Dennis.

Target Market(s)

Investors
Clients

Coding

Coded - Design and coding required

Number of Pages Required

5+ page

Font styles to use
Sans Serif

Colors
886aae
3176b5
00a990
f68e4d
f04a50
e667a6

Requirements
Must have
• WordPress Coding

Checkout this Website for look and feel - its cool:
www.qvr-example.com

Harbor Crest Partners
(Harbor Crest Holdings LLP)
London
E9 4ZX
United Kingdom

www.HarborCrestPartners-example.com
Nice to have
• Sophisticated colour palette - black/ brown/ blue/ purple/

```html
<!DOCTYPE html>
<html lang="en">
<head>
<meta charset="utf-8">
<title>Harbor Crest Holdings</title>
<link rel="stylesheet" href="https://fonts.googleapis.com/css2?family=Roboto:wght@400;500;700;900&display=swap">
<style>
:root{
  --orange:#f0763a;
  --blue:#1f5fb0;
  --navy:#1b1c30;
  --ink:#1d1d1f;
  --body:#3c3c44;
  --muted:#f5f6fa;
  --line:#e3e3e8;
  --white:#fff;
  --teal:#0f9f86;
  --sand:#f7f3ec;
}
*{margin:0;padding:0;box-sizing:border-box}
html,body{width:1200px;height:4979px;overflow:hidden}
body{position:relative;font-family:'Roboto',Arial,sans-serif;color:var(--ink);background:var(--white)}
.abs{position:absolute}
.photo{position:absolute;display:block}

/* hero */
.hero{position:absolute;left:0;top:0;width:1200px;height:810px;background:radial-gradient(ellipse at 55% 40%,#8a6a55 0%,#3f4a33 38%,#1f2c1c 75%,#142012 100%)}
.hero-phone{left:38px;top:60px;color:#fff;display:flex;gap:14px;align-items:center}
.hero-phone small{display:block;font-size:13px}
.hero-phone b{display:block;font-size:21px;font-weight:700;letter-spacing:.5px}
.brand{left:0;width:1200px;top:52px;text-align:center;color:#fff;font-size:46px;font-weight:700;letter-spacing:.5px}
.btn-ghost{border:2px solid #fff;border-radius:24px;color:#fff;font-size:15px;font-weight:700;display:flex;align-items:center;justify-content:center}
.menu-icon{left:1134px;top:64px;width:26px}
.menu-icon span{display:block;height:4px;background:#fff;margin-bottom:5px}
.hero-title{left:62px;top:290px;color:#fff;font-size:58px;font-weight:700;line-height:66px}
.btn-hero{left:64px;top:454px;width:203px;height:47px;border:2px solid var(--orange);border-radius:24px;color:#fff;font-weight:700;font-size:16px;display:flex;align-items:center;justify-content:center}
.dots{left:560px;top:703px;display:flex;gap:7px}
.dots span{width:14px;height:14px;border-radius:50%;border:2px solid #fff}
.dots span.on{background:#fff}

/* headings */
.section-title{left:0;width:1200px;text-align:center;font-size:31px;font-weight:700;color:var(--ink)}
.underline{left:565px;width:70px;height:3px;background:var(--blue)}

/* sectors */
.sector{background:#fff;width:228px;box-shadow:0 3px 14px rgba(0,0,0,.12);text-align:center}
.sector .photo{position:relative;width:228px;height:180px}
.sector h3{font-size:17px;font-weight:500;margin:24px 0 14px}
.sector p{font-size:13.5px;line-height:17px;color:var(--body);padding:0 24px}
.btn-outline{display:inline-flex;align-items:center;justify-content:center;border:2px solid var(--orange);border-radius:20px;color:var(--orange);font-weight:700;font-size:14px}
.sector .btn-outline{width:118px;height:31px;font-size:12px;margin:18px 0 22px}
.arrow-btn{width:30px;height:30px;border:1.5px solid #555;border-radius:50%;display:flex;align-items:center;justify-content:center}

/* feature rows */
.frame{border:2px solid var(--orange)}
.texture{background:var(--sand)}
.feature-kicker{font-size:38px;font-weight:400;color:var(--orange);line-height:46px}
.feature-kicker span{color:var(--ink)}
.feature-head{font-size:38px;font-weight:700;line-height:46px}
.feature-copy{font-size:13.8px;line-height:21.7px;color:var(--body)}
.feature .btn-outline{width:143px;height:39px}
.connector{border-top:2px solid var(--orange);border-right:2px solid var(--orange)}

/* blog */
.post{background:#fff;width:290px;border:1px solid var(--line);box-shadow:0 2px 8px rgba(0,0,0,.06)}
.post .photo{position:relative;width:100%;height:199px}
.badge{position:absolute;right:20px;top:20px;width:43px;height:43px;border-radius:50%;background:var(--teal);color:#fff;font-size:10px;font-weight:700;text-align:center;line-height:12px;padding-top:9px}
.post h4{font-size:15px;font-weight:700;line-height:20px;padding:24px 22px 0;text-transform:uppercase}
.post p{font-size:13.5px;line-height:21px;color:var(--body);padding:14px 22px 0}
.btn-dark{display:inline-flex;align-items:center;gap:6px;margin:18px 22px 0;height:36px;padding:0 18px;border:2px solid var(--navy);border-radius:18px;font-size:12px;font-weight:500}

/* testimonials */
.testimonials{left:0;top:3827px;width:1200px;height:620px;background:var(--muted)}
.quote-card{left:406px;top:4019px;width:572px;height:309px;background:#fff;box-shadow:0 2px 10px rgba(0,0,0,.06)}
.quote-copy{left:505px;top:4064px;width:425px;font-size:14px;line-height:21px;color:var(--body)}
.quote-name{left:505px;top:4249px;font-size:15px;font-weight:500}
.quote-role{left:505px;top:4274px;font-size:14px;font-weight:500}
.quote-mark{font-family:Georgia,serif;font-size:110px;color:#d3d3d8;line-height:1}
.nav-dot{width:34px;height:34px;border-radius:50%;background:var(--blue);display:flex;align-items:center;justify-content:center}

/* footer */
.footer-bg{left:0;top:4400px}
.f-title{font-size:15.5px;font-weight:700;color:#fff;letter-spacing:.4px}
.f-text{font-size:13.5px;line-height:20px;color:#e6e6ee}
.f-input{width:273px;height:37px;background:#fff;font-size:11px;color:#555;padding:12px 18px}
.f-btn{left:145px;top:4779px;width:135px;height:33px;background:var(--orange);color:#fff;font-size:13.5px;font-weight:700;display:flex;align-items:center;justify-content:center}
.f-links a{display:block;color:#e6e6ee;font-size:13.5px;text-decoration:none;height:27px}
.f-social div{display:flex;align-items:center;gap:10px;color:#e6e6ee;font-size:13.5px;height:34px}
.f-social i{width:24px;height:24px;border:1.5px solid #e6e6ee;border-radius:50%}
.f-rule{left:0;top:4871px;width:1200px;height:1px;background:#2f3048}
.f-bottom{top:4918px;font-size:13.5px;color:#e6e6ee}
</style>
</head>
<body>

<!-- Hero -->
<section class="hero" role="img" aria-label="Photo of a woman holding a green fern leaf against dark foliage"></section>
<div class="abs hero-phone">
  <svg width="38" height="38" viewBox="0 0 24 24" fill="none" stroke="#fff" stroke-width="1.6"><path d="M5 3h4l2 5-3 2a11 11 0 0 0 6 6l2-3 5 2v4a2 2 0 0 1-2 2A17 17 0 0 1 3 5a2 2 0 0 1 2-2z"/></svg>
  <div><small>Call us at</small><b>0200 555 0147</b></div>
</div>
<div class="abs brand">Harbor Crest</div>
<div class="abs btn-ghost" style="left:943px;top:56px;width:161px;height:43px">GET STARTED</div>
<div class="abs menu-icon"><span></span><span></span><span></span></div>
<h1 class="abs hero-title">Beauty and<br>Personal Care</h1>
<div class="abs btn-hero">LEARN MORE</div>
<div class="abs dots"><span class="on"></span><span></span><span></span><span></span></div>

<!-- Sectors -->
<h2 class="abs section-title" style="top:872px">OUR SECTORS</h2>
<div class="abs underline" style="top:925px"></div>
<div class="abs arrow-btn" style="left:48px;top:1150px"><svg width="10" height="12" viewBox="0 0 10 12"><path d="M7 1 2 6l5 5" fill="none" stroke="#333" stroke-width="1.5"/></svg></div>
<div class="abs arrow-btn" style="left:1122px;top:1150px"><svg width="10" height="12" viewBox="0 0 10 12"><path d="m3 1 5 5-5 5" fill="none" stroke="#333" stroke-width="1.5"/></svg></div>

<article class="abs sector" style="left:95px;top:982px">
  <div class="photo" role="img" aria-label="Photo of a timber house with a garden" style="background:linear-gradient(180deg,#9fb4c6 0%,#6b5a4c 55%,#4d5a3a 100%)"></div>
  <h3>Real Estate</h3>
  <p>Nemo enim ipsam luptatem quia voluptas sit aspernatur aut odit aut fugit, sed quia consequuntur magni</p>
  <span class="btn-outline">READ MORE</span>
</article>
<article class="abs sector" style="left:356px;top:997px">
  <div class="photo" role="img" aria-label="Photo of hands shopping online on a laptop" style="background:linear-gradient(180deg,#2d2f3a 0%,#8a8f9a 50%,#3a3430 100%)"></div>
  <h3>E-Commerce</h3>
  <p>Nemo enim ipsam luptatem quia voluptas sit aspernatur aut odit aut fugit, sed quia consequuntur magni</p>
  <span class="btn-outline">READ MORE</span>
</article>
<article class="abs sector" style="left:615px;top:982px">
  <div class="photo" role="img" aria-label="Photo of a doctor using a tablet with digital health overlay" style="background:linear-gradient(135deg,#0f3f5e 0%,#2f87a8 55%,#c9dbe6 100%)"></div>
  <h3>Healthcare</h3>
  <p>Nemo enim ipsam luptatem quia voluptas sit aspernatur aut odit aut fugit, sed quia consequuntur magni</p>
  <span class="btn-outline">READ MORE</span>
</article>
<article class="abs sector" style="left:876px;top:997px">
  <div class="photo" role="img" aria-label="Photo of a woman applying skincare products" style="background:linear-gradient(135deg,#d9b79a 0%,#9a6a4e 55%,#e5d4c4 100%)"></div>
  <h3>Beauty &amp; Personal Care</h3>
  <p>Nemo enim ipsam luptatem quia voluptas sit aspernatur aut odit aut fugit, sed quia consequuntur magni</p>
  <span class="btn-outline">READ MORE</span>
</article>

<!-- Welcome -->
<section class="feature">
  <div class="abs texture" role="img" aria-label="Dotted texture" style="left:0;top:1840px;width:473px;height:145px"></div>
  <div class="abs frame" style="left:130px;top:1473px;width:435px;height:450px"></div>
  <div class="photo" role="img" aria-label="Photo of a hand using a tablet to shop online" style="left:145px;top:1488px;width:437px;height:449px;background:linear-gradient(135deg,#d8c8bd 0%,#9c8f88 45%,#3a3638 100%)"></div>
  <div class="abs connector" style="left:582px;top:1529px;width:141px;height:24px"></div>
  <h2 class="abs feature-kicker" style="left:669px;top:1572px">Welcome to <span>Harbor Crest</span></h2>
  <h2 class="abs feature-head" style="left:669px;top:1620px">Holdings</h2>
  <p class="abs feature-copy" style="left:669px;top:1686px;width:402px">Nemo enim ipsam voluptatem quia voluptas sit aspernatur aut odit aut fugit, sed quia consequuntur magni dolores eos qui ratione voluptatem sequi nesciunt. Neque porro quisquam est, qui dolorem ipsum quia dolor sit amet, consectetur, adipisci velit, sed quia non numquam eius modi tempora incidunt ut labore et dolore magnam aliquam quaerat voluptatem. Ut enim ad minima veniam, quis nostrum</p>
  <span class="abs btn-outline" style="left:669px;top:1869px">READ MORE</span>
</section>

<!-- Expertise -->
<section class="feature">
  <div class="abs texture" role="img" aria-label="Dotted texture" style="left:1073px;top:2381px;width:127px;height:151px"></div>
  <div class="abs texture" role="img" aria-label="Dotted texture" style="left:709px;top:2493px;width:491px;height:39px"></div>
  <div class="abs frame" style="left:618px;top:2016px;width:435px;height:450px"></div>
  <div class="photo" role="img" aria-label="Photo of a smiling man with headphones waving at his laptop" style="left:634px;top:2032px;width:435px;height:448px;background:linear-gradient(135deg,#e6e1da 0%,#a49c92 40%,#2f3f66 75%,#1f2c4a 100%)"></div>
  <h2 class="abs feature-kicker" style="left:128px;top:2091px">Expertise</h2>
  <div class="abs connector" style="left:300px;top:2115px;width:160px;height:20px"></div>
  <p class="abs" style="left:128px;top:2151px;font-size:24px;line-height:32px;color:var(--ink)">Sed ut perspiciatis unde omnis<br>iste natus sit voluptatem</p>
  <p class="abs feature-copy" style="left:130px;top:2231px;width:405px">Nemo enim ipsam voluptatem quia voluptas sit aspernatur aut odit aut fugit, sed quia consequuntur magni dolores eos qui ratione voluptatem sequi nesciunt. Neque porro quisquam est, qui dolorem ipsum quia dolor sit amet, consectetur, adipisci velit, sed quia non numquam eius modi tempora incidunt ut labore et dolore magnam aliquam quaerat voluptatem. Ut enim ad minima veniam, quis nostrum</p>
  <span class="abs btn-outline" style="left:130px;top:2412px">READ MORE</span>
</section>

<!-- Global Outlook -->
<section class="feature">
  <div class="abs texture" role="img" aria-label="Dotted texture" style="left:0;top:2923px;width:473px;height:151px"></div>
  <div class="abs frame" style="left:130px;top:2561px;width:435px;height:450px"></div>
  <div class="photo" role="img" aria-label="Photo of a woman in a yellow top reading a tablet against a pink wall" style="left:145px;top:2577px;width:437px;height:448px;background:linear-gradient(90deg,#e8406a 0%,#f05b7a 45%,#e7d23a 70%,#f04d70 100%)"></div>
  <div class="abs connector" style="left:582px;top:2617px;width:141px;height:25px"></div>
  <h2 class="abs feature-kicker" style="left:669px;top:2660px">Global Outlook</h2>
  <h2 class="abs feature-head" style="left:669px;top:2706px">Nemo enim voluptatem</h2>
  <p class="abs feature-copy" style="left:669px;top:2775px;width:402px">Nemo enim ipsam voluptatem quia voluptas sit aspernatur aut odit aut fugit, sed quia consequuntur magni dolores eos qui ratione voluptatem sequi nesciunt. Neque porro quisquam est, qui dolorem ipsum quia dolor sit amet, consectetur, adipisci velit, sed quia non numquam eius modi tempora incidunt ut labore et dolore magnam aliquam quaerat voluptatem. Ut enim ad minima veniam, quis nostrum</p>
  <span class="abs btn-outline" style="left:669px;top:2957px">READ MORE</span>
</section>

<!-- Blog -->
<h2 class="abs section-title" style="top:3146px;font-size:36px">FROM THE BLOG</h2>
<div class="abs underline" style="top:3206px"></div>

<article class="abs post" style="left:143px;top:3276px;height:441px">
  <div class="photo" role="img" aria-label="Photo of a man thinking at his laptop in a cafe" style="background:linear-gradient(135deg,#c89a6c 0%,#6e5a4a 50%,#2e2a28 100%)"><span class="badge">OCT<br>2020</span></div>
  <h4>Nemo enim ipsam volupta quia voluptas sit</h4>
  <p>Lorem ipsum dolor sit amet, contetur adipiscing elit, sed do eiusmod mpor incididunt ut labore et dolore magna aliqua. Ut enim ad minim</p>
  <span class="btn-dark">READ MORE <svg width="9" height="9" viewBox="0 0 10 10"><path d="M0 5h7M4 1l4 4-4 4" stroke="#1b1c30" stroke-width="2" fill="none"/></svg></span>
</article>
<article class="abs post" style="left:456px;top:3261px;height:443px">
  <div class="photo" role="img" aria-label="Photo of a team planning with sticky notes on a glass wall" style="background:linear-gradient(135deg,#d8e4ec 0%,#7f93a6 50%,#2e3a4e 100%)"><span class="badge">OCT<br>2020</span></div>
  <h4>Nemo enim ipsam volupta quia voluptas sit</h4>
  <p>Lorem ipsum dolor sit amet, contetur adipiscing elit, sed do eiusmod mpor incididunt ut labore et dolore magna aliqua. Ut enim ad minim</p>
  <span class="btn-dark">READ MORE <svg width="9" height="9" viewBox="0 0 10 10"><path d="M0 5h7M4 1l4 4-4 4" stroke="#1b1c30" stroke-width="2" fill="none"/></svg></span>
</article>
<article class="abs post" style="left:767px;top:3276px;height:441px">
  <div class="photo" role="img" aria-label="Photo of colleagues collaborating in a bright office" style="background:linear-gradient(135deg,#cfd8e2 0%,#6a7ca0 50%,#2b3050 100%)"><span class="badge">OCT<br>2020</span></div>
  <h4>Nemo enim ipsam volupta quia voluptas sit</h4>
  <p>Lorem ipsum dolor sit amet, contetur adipiscing elit, sed do eiusmod mpor incididunt ut labore et dolore magna aliqua. Ut enim ad minim</p>
  <span class="btn-dark" style="border-color:var(--teal)">READ MORE <svg width="9" height="9" viewBox="0 0 10 10"><path d="M0 5h7M4 1l4 4-4 4" stroke="#1b1c30" stroke-width="2" fill="none"/></svg></span>
</article>

<!-- Testimonials -->
<section class="abs testimonials"></section>
<h2 class="abs section-title" style="top:3896px;font-size:34px">WHAT OUR CUSTOMERS SAY</h2>
<div class="abs underline" style="top:3958px;left:560px;width:80px"></div>
<div class="abs quote-card"></div>
<div class="photo" role="img" aria-label="Photo of a businessman standing among glass towers at sunset" style="left:222px;top:4019px;width:184px;height:309px;background:linear-gradient(180deg,#9a5a4a 0%,#d9a27a 45%,#f4e6d6 70%,#3a3a4a 100%)"></div>
<div class="abs quote-mark" style="left:432px;top:4020px">&ldquo;</div>
<div class="abs quote-mark" style="left:850px;top:4238px">&rdquo;</div>
<p class="abs quote-copy">Sed ut perspiciatis unde omnis iste natus error sit voluptatem accusantium doloremque laudantium, totam rem aperiam, eaque ipsa quae ab illo inventore veritatis et quasi architecto beatae vitae dicta sunt explicabo. Nemo enim ipsam voluptatem quia voluptas sit aspernatur aut odit aut fugit, sed quia consequuntur magni dolores eos qui ratione voluptatem sequi nesciunt. Neque porro quisquam est, qui dolorem ipsum quia dolor sit amet, consectetur, adipisci velit, sed quia non numquam</p>
<p class="abs quote-name">Maren Holloway</p>
<p class="abs quote-role">Nemo enim ipsam voluptatem</p>
<div class="abs nav-dot" style="left:202px;top:4170px"><svg width="10" height="12" viewBox="0 0 10 12"><path d="M7 1 2 6l5 5" fill="none" stroke="#fff" stroke-width="2"/></svg></div>
<div class="abs nav-dot" style="left:963px;top:4170px"><svg width="10" height="12" viewBox="0 0 10 12"><path d="m3 1 5 5-5 5" fill="none" stroke="#fff" stroke-width="2"/></svg></div>

<!-- Footer -->
<svg class="abs footer-bg" width="1200" height="579" viewBox="0 0 1200 579">
  <polygon points="60,105 348,13 720,70 348,32" fill="var(--blue)"/>
  <polygon points="0,133 348,30 1200,145 1200,579 0,579" fill="var(--navy)"/>
</svg>

<h3 class="abs f-title" style="left:145px;top:4572px">SIGN UP FOR NEWSLETTER</h3>
<p class="abs f-text" style="left:145px;top:4614px;width:290px">Excepteur sint occaecat cupidatat non proident, sunt in culpa qui officia deserunt</p>
<div class="abs f-input" style="left:145px;top:4674px">Enter Name</div>
<div class="abs f-input" style="left:145px;top:4725px">Enter email</div>
<div class="abs f-btn">SUBSCRIBE</div>

<h3 class="abs f-title" style="left:487px;top:4568px">CONTACT US</h3>
<svg class="abs" style="left:490px;top:4622px" width="16" height="20" viewBox="0 0 16 20"><path d="M8 0a7 7 0 0 0-7 7c0 5 7 13 7 13s7-8 7-13a7 7 0 0 0-7-7zm0 10a3 3 0 1 1 0-6 3 3 0 0 1 0 6z" fill="#fff"/></svg>
<p class="abs f-text" style="left:524px;top:4616px">Harbor Crest<br>20 enim ipsam vptatem<br>quia voluptas sit</p>
<svg class="abs" style="left:490px;top:4680px" width="17" height="17" viewBox="0 0 24 24"><path d="M5 2h4l2 5-3 2a11 11 0 0 0 6 6l2-3 5 2v4a2 2 0 0 1-2 2A17 17 0 0 1 3 4a2 2 0 0 1 2-2z" fill="#fff"/></svg>
<p class="abs f-text" style="left:524px;top:4676px">Phone:<br>555 0100 2200</p>
<svg class="abs" style="left:490px;top:4733px" width="18" height="14" viewBox="0 0 18 14"><rect width="18" height="14" rx="1" fill="#fff"/><path d="m1 1 8 6 8-6" stroke="var(--navy)" stroke-width="1.5" fill="none"/></svg>
<p class="abs f-text" style="left:524px;top:4729px">Email:<br>info@harborcrest-example.com</p>

<h3 class="abs f-title" style="left:779px;top:4568px">QUICK LINKS</h3>
<nav class="abs f-links" style="left:783px;top:4614px">
  <a>Home</a><a>About Us</a><a>Expertise</a><a>Global Outlook</a><a>Sectors</a><a>Management</a><a>Media</a><a>Contact Us</a>
</nav>

<h3 class="abs f-title" style="left:959px;top:4568px">FOLLOW US</h3>
<div class="abs f-social" style="left:959px;top:4610px">
  <div><i></i>Newsfeed</div><div><i></i>Updates</div><div><i></i>Circles</div><div><i></i>Videos</div>
</div>

<div class="abs f-rule"></div>
<p class="abs f-bottom" style="left:145px">(c) 2020 Harbor Crest | All Rights Reserved</p>
<p class="abs f-bottom" style="left:875px">Cookies and Privacy policy</p>

</body>
</html>
```